Audit/Compliance company needs Business Card Template

We are after a Business Card Template that we can modify internally to update details as people change positions.
We are an Australian based company specalising in Auditing and Quality/OHS systems development. - See www.brimfieldreview.com.au for more information
We would like the desings to be based around our logo and colours assocaited with it (attached for your information) however we are very open as to how the cards are designed.
We are looking for something quite edgy and mordern but it must have a professional/compliance feel to it (if possible).
The main details we would like to include within the card template are:
Name
Position Title
Postal Address
Phone Number
Mobile Number
Email Address
Website
The cards will be printed through lanterly press on Glossy paper so it should reflect the requirements below
Full Bleed Size (starting document size)
90 x 52 mm
1062 x 615 pixels
Document Trim Size (final size after being cut)
87 x 49 mm
1028 x 579 pixels
Resolution
300 DPI

```html
<!DOCTYPE html>
<html lang="en">
<head>
<meta charset="utf-8">
<title>Brimfield Review &amp; Compliance — Business Card</title>
<link rel="stylesheet" href="https://fonts.googleapis.com/css2?family=Open+Sans:wght@300;400;600;700&display=swap">
<style>
  :root {
    --paper: #f3f3f2;
    --orange: #f26522;
    --ink-dark: #14142b;
    --ink: #4d4d4d;
    --brand-ink: #3a3a3a;
  }
  * { margin: 0; padding: 0; box-sizing: border-box; }
  html, body { width: 1200px; height: 676px; overflow: hidden; background: var(--paper); }
  .card {
    position: relative;
    width: 1200px;
    height: 676px;
    background: var(--paper);
    font-family: "Open Sans", sans-serif;
    color: var(--ink);
  }
  .holder { position: absolute; right: 42px; top: 30px; text-align: right; }
  .holder-name { font-size: 31px; font-weight: 700; color: var(--orange); line-height: 1.2; }
  .holder-position { font-size: 26px; font-weight: 300; color: var(--orange); line-height: 1.25; }
  .edge-tab { position: absolute; right: 0; top: 35px; width: 14px; height: 68px; background: var(--orange); }
  .brand { position: absolute; left: 36px; top: 128px; display: flex; align-items: center; gap: 26px; }
  .brand-mark { width: 150px; height: 130px; background: var(--orange); }
  .brand-name {
    font-size: 38px; font-weight: 400; color: var(--brand-ink);
    letter-spacing: 1px; line-height: 1.2; text-transform: uppercase;
  }
  .divider { position: absolute; left: 0; top: 337px; width: 1200px; height: 2px; background: var(--orange); }
  .postal { position: absolute; left: 35px; top: 405px; font-size: 23px; line-height: 1.5; }
  .postal-label { font-weight: 700; color: var(--ink-dark); }
  .contacts { position: absolute; left: 713px; top: 413px; font-size: 23px; border-collapse: collapse; }
  .contacts th { text-align: left; font-weight: 700; color: var(--ink); padding: 0 10px 9px 0; }
  .contacts td { font-weight: 400; padding: 0 0 9px 0; }
</style>
</head>
<body>
  <div class="card">
    <div class="holder">
      <div class="holder-name">Name Surname</div>
      <div class="holder-position">Position</div>
    </div>
    <div class="edge-tab"></div>

    <div class="brand">
      <div class="brand-mark"></div>
      <div class="brand-name">Brimfield Review<br>&amp; Compliance</div>
    </div>

    <div class="divider"></div>

    <div class="postal">
      <div><span class="postal-label">Postal Address</span>:</div>
      <div>Level 3, 48 Harbour Lane,</div>
      <div>Sydney, Australia</div>
    </div>

    <table class="contacts">
      <tr><th>Ph:</th><td>1300 555 214</td></tr>
      <tr><th>M:</th><td>1300 555 214</td></tr>
      <tr><th>E:</th><td>email.adress@brimfield-review.com.au</td></tr>
      <tr><th>W:</th><td>www.brimfieldreview.com.au</td></tr>
    </table>
  </div>
</body>
</html>
```